Soy Candle Labels

We sell soy candles in recycled wine bottles. The wine bottle is cut in half and filled with pure and natural soy wax and scented with essential oils.
Our product represents good use of up cycling materials for a better use. The product is all natural and eco friendly.
You can see good use of labels and branding for a company in America that does the same thing http://larkmeadow7wicks.example/
Trya dn keep the label uncomplicated like the above labels.
We will need an area to hand stamp the scent. Similar to the labels used on the above website.
We would prefer to use a white or off white paper label with gold or bronze printing - limit the use of colour and keep the label simple and sophisticated.
Emberlace Candle Co. is our company name. Emberlace being the predominant name and candle co. written small underneath right justified.
Die cut labels might look better than a rectangle.
Dimensions should be 90mm Wide x 90mm High
The final design should communicate a professional and quality product. But stay modern and professional. Clean, elegant and sophisticated.
Can use wording such as: Hand Poured, Premium Soy Wax, All Natural, Up cycled
Have a look at the attached image for the look and feel we are going for.
Updates
Designers are having a little bit of trouble interpreting the brief into a viable design. To assist perhaps you can look at WINE LABELS on google images. Design your label around an existing style wine label to give the canld ethe feel of being a bottle of wine. Get creative! :)
Reason: We require more designs. We havnt quite got what were looking for.
Please see brief.

```html
<!DOCTYPE html>
<html lang="en">
<head>
<meta charset="utf-8">
<title>Emberlace Candle Co. — Soy Candle Label</title>
<link rel="stylesheet" href="https://fonts.googleapis.com/css2?family=Cormorant+Garamond:wght@500&display=swap">
<style>
  :root {
    --paper: #ffffff;
    --bronze: #b86c2c;
    --ink-grey: #666666;
    --rule-grey: #7a7a7a;
    --serif: "Cormorant Garamond", Georgia, serif;
  }
  html, body {
    margin: 0;
    padding: 0;
    overflow: hidden;
    background: var(--paper);
  }
  .label {
    position: relative;
    width: 1200px;
    height: 1200px;
    background: var(--paper);
    font-family: var(--serif);
    font-weight: 500;
    overflow: hidden;
  }
  .top-band {
    position: absolute;
    left: 0; top: 0;
    width: 100%;
    height: 10px;
    background: var(--bronze);
  }
  .tagline {
    position: absolute;
    left: 70px;
    top: 284px;
    margin: 0;
    font-size: 34px;
    line-height: 1;
    letter-spacing: 0.03em;
    text-transform: uppercase;
    color: var(--ink-grey);
    white-space: nowrap;
  }
  .tagline .divider { margin: 0 14px; }
  .double-rule {
    position: absolute;
    left: 0;
    top: 342px;
    width: 692px;
    height: 10px;
  }
  .scent-stamp {
    position: absolute;
    left: 820px;
    top: 210px;
    width: 340px;
    height: 310px;
  }
  .scent-stamp .scent-word {
    position: absolute;
    left: 0;
    top: 155px;
    transform: translate(0, -50%) rotate(-90deg);
    transform-origin: center;
    font-size: 28px;
    letter-spacing: 0.04em;
    color: var(--ink-grey);
    line-height: 1;
    margin-left: -24px;
  }
  .scent-stamp svg {
    position: absolute;
    left: 36px;
    top: 0;
  }
  .brand {
    position: absolute;
    right: 57px;
    top: 700px;
    margin: 0;
    text-align: right;
    color: var(--bronze);
    font-weight: 500;
  }
  .brand .brand-name {
    display: block;
    font-size: 172px;
    line-height: 1;
    letter-spacing: 0.02em;
    text-transform: uppercase;
  }
  .brand .brand-sub {
    display: block;
    font-size: 48px;
    line-height: 1;
    letter-spacing: 0.04em;
    text-transform: uppercase;
    margin-top: 18px;
  }
  .origin, .weight {
    position: absolute;
    top: 1120px;
    margin: 0;
    font-size: 29px;
    line-height: 1;
    letter-spacing: 0.02em;
    text-transform: uppercase;
    color: var(--ink-grey);
    white-space: nowrap;
  }
  .origin { left: 68px; }
  .weight { right: 69px; }
</style>
</head>
<body>
  <main class="label">
    <div class="top-band"></div>

    <p class="tagline">Hand Poured<span class="divider">|</span>All Natural Soy</p>

    <svg class="double-rule" viewBox="0 0 692 10" aria-hidden="true">
      <line x1="0" y1="2" x2="692" y2="2" stroke="var(--rule-grey)" stroke-width="2"/>
      <line x1="0" y1="8" x2="692" y2="8" stroke="var(--rule-grey)" stroke-width="2"/>
    </svg>

    <div class="scent-stamp">
      <span class="scent-word">SCENT</span>
      <svg width="304" height="304" viewBox="0 0 304 304" role="img" aria-label="Blank circle for hand stamping the scent">
        <circle cx="152" cy="152" r="150" fill="none" stroke="var(--ink-grey)" stroke-width="3"/>
      </svg>
    </div>

    <h1 class="brand">
      <span class="brand-name">Emberlace</span>
      <span class="brand-sub">Candle Co.</span>
    </h1>

    <p class="origin">Product of Australia</p>
    <p class="weight">320 gm. Premium Soy Wax</p>
  </main>
</body>
</html>
```